Mastering Modern Vineyard Management

size of the ad - 8”x 10.75" plus 0.25" bleed
I would like an ad for a magazine that will stand out and make people want to read the ad.
The ad should not be crowded and people reading the ad will be able to read the text.
I would like it to be a creative and modern-day design.
the list of topics should not be the focus of the ad.
the text is attached.
If you decide to use people in the ad then please no ladies.
please note that leave over 1 inch for the bottom of the footer

```html
<!DOCTYPE html>
<html lang="en">
<head>
<meta charset="utf-8">
<title>Mastering Modern Vineyard Management – Course Ad</title>
<link href="https://fonts.googleapis.com/css2?family=Oswald:wght@700&family=Arimo:ital,wght@0,400;0,700;1,400;1,700&display=swap" rel="stylesheet">
<style>
  :root {
    --sky-top: #1f5f98;
    --sky-mid: #4f86b8;
    --glass-dark: #14223b;
    --glass-light: #9fb8cf;
    --panel-top: rgba(6, 10, 38, 0.92);
    --panel-bottom: rgba(48, 48, 52, 0.9);
    --white: #ffffff;
    --soft-white: #e6e8ee;
    --muted: #c9ccd4;
    --rule: rgba(255, 255, 255, 0.75);
  }
  * { margin: 0; padding: 0; box-sizing: border-box; }
  html, body { width: 893px; height: 1200px; overflow: hidden; background: var(--sky-top); }
  .ad {
    position: relative;
    width: 893px;
    height: 1200px;
    overflow: hidden;
    font-family: "Arimo", Arial, sans-serif;
    color: var(--white);
  }
  .backdrop {
    position: absolute;
    inset: 0;
    background:
      linear-gradient(160deg, transparent 35%, rgba(20, 34, 59, 0.85) 60%, var(--glass-dark) 100%),
      linear-gradient(200deg, var(--sky-top) 0%, var(--sky-mid) 30%, var(--glass-light) 55%, #5d7d9c 75%, #2a3d58 100%);
  }
  .headline {
    position: absolute;
    left: -2px;
    top: -34px;
    font-family: "Oswald", "Arial Narrow", sans-serif;
    font-weight: 700;
    font-size: 124px;
    line-height: 1;
    letter-spacing: 0;
    white-space: nowrap;
    transform: scaleX(0.97);
    transform-origin: left top;
    text-shadow: 2px 3px 4px rgba(0, 0, 0, 0.35);
  }
  .panel {
    position: absolute;
    left: 163px;
    top: 124px;
    width: 730px;
    height: 973px;
    background: linear-gradient(180deg, var(--panel-top) 0%, rgba(12, 16, 48, 0.85) 55%, var(--panel-bottom) 100%);
  }
  .course-title {
    position: absolute;
    left: 42px;
    top: 46px;
    font-weight: 700;
    font-size: 42px;
    line-height: 52px;
    letter-spacing: 0.5px;
    text-transform: uppercase;
    white-space: nowrap;
  }
  .tagline {
    position: absolute;
    left: 42px;
    top: 165px;
    font-style: italic;
    font-size: 29px;
    line-height: 44px;
    letter-spacing: 4px;
    text-transform: uppercase;
    color: var(--soft-white);
    white-space: nowrap;
  }
  .location {
    position: absolute;
    left: 52px;
    top: 296px;
    font-weight: 700;
    font-size: 35px;
  }
  .location-rule {
    position: absolute;
    left: 42px;
    top: 348px;
    width: 398px;
    height: 1px;
    background: var(--rule);
  }
  .schedule {
    position: absolute;
    left: 52px;
    top: 357px;
    list-style: none;
    font-weight: 700;
    font-size: 25px;
    line-height: 37px;
  }
  .early-bird {
    position: absolute;
    left: 52px;
    top: 505px;
    color: var(--muted);
  }
  .early-bird-title { font-weight: 700; font-style: italic; font-size: 21px; line-height: 28px; }
  .early-bird-note { font-size: 21px; line-height: 28px; }
  .topics {
    position: absolute;
    left: 52px;
    top: 623px;
  }
  .topics-heading { font-weight: 700; font-size: 20px; line-height: 28px; }
  .topics-list { list-style: none; font-size: 20px; line-height: 28px; color: var(--soft-white); }
</style>
</head>
<body>
  <div class="ad">
    <div class="backdrop" role="img" aria-label="Photograph of a modern glass building reflecting a blue sky with clouds"></div>

    <div class="headline">VINEYARD COURSE</div>

    <section class="panel">
      <h1 class="course-title">Mastering Modern<br>Vineyard Management</h1>
      <p class="tagline">Investing in knowledge is<br>investing in opportunities.</p>

      <h2 class="location">Glenbrook</h2>
      <div class="location-rule"></div>
      <ul class="schedule">
        <li>10 -Tuesday evenings sessions</li>
        <li>Starting Feb.28</li>
        <li>Limited Partial Scholarships</li>
      </ul>

      <div class="early-bird">
        <p class="early-bird-title">Early Bird Special</p>
        <p class="early-bird-note">For those that started or would like to go into viticulture</p>
      </div>

      <div class="topics">
        <p class="topics-heading">Topics: partial listing</p>
        <ul class="topics-list">
          <li>Vineyard site selection strategies</li>
          <li>Soil analysis</li>
          <li>Irrigation</li>
          <li>Canopy care</li>
          <li>Pest and disease control</li>
          <li>Vineyard legal basics</li>
          <li>Harvest timing</li>
          <li>Grape sales</li>
          <li>Working with wineries</li>
          <li>Farm finance basics</li>
        </ul>
      </div>
    </section>
  </div>
</body>
</html>
```